Pemberlux: Smart Quotes for Wine Lovers

Hello. I am completing book of quotes for wine lovers. Need the text formatted so that it is easy to read and aesthetically pleasing...modern, clean, smart. Number the pages. The cover is complete. Book is small square. 7.5 by 7.5 inches. If you want to show me first few pages that would be awesome. Thank you!
Updates

I edited the quotes so if you downloaded first ones, please grab these ones instead, thank you! 

Target Market(s)

wine lovers. Urban. Modern.

Industry/Entity Type

Quotes

Requirements
Should not have
• No color. black and white only.

```html
<!DOCTYPE html>
<html lang="en">
<head>
<meta charset="utf-8">
<title>Pemberlux: Smart Quotes for Wine Lovers — Spread 24–25</title>
<link rel="stylesheet" href="https://fonts.googleapis.com/css2?family=PT+Sans:wght@400;700&display=swap">
<style>
  :root {
    --ink: #000000;
    --paper: #ffffff;
    --muted: #7a7a7a;
  }
  * { margin: 0; padding: 0; box-sizing: border-box; }
  html, body {
    width: 1200px;
    height: 600px;
    overflow: hidden;
    background: var(--paper);
  }
  .spread {
    position: relative;
    width: 1200px;
    height: 600px;
    display: flex;
    font-family: "PT Sans", Verdana, sans-serif;
  }
  .page {
    position: relative;
    width: 600px;
    height: 600px;
  }
  .page--dark { background: var(--ink); color: var(--paper); }
  .page--light { background: var(--paper); color: var(--ink); }

  .quote {
    position: absolute;
    font-weight: 400;
    font-size: 39px;
    line-height: 44px;
    letter-spacing: 0.5px;
  }
  .page--dark .quote { left: 95px; top: 122px; width: 300px; }
  .page--light .quote { right: 95px; top: 122px; width: 380px; text-align: right; }

  .attribution {
    display: block;
    margin-top: 14px;
    font-size: 13px;
    line-height: 16px;
    font-style: normal;
    letter-spacing: 1.4px;
    text-transform: uppercase;
  }
  .page--light .attribution { margin-top: 12px; }

  .bio {
    position: absolute;
    top: 518px;
    font-size: 7.5px;
    line-height: 9.5px;
    font-weight: 700;
  }
  .page--dark .bio { right: 63px; width: 300px; text-align: right; color: var(--paper); }
  .page--light .bio { left: 62px; width: 300px; color: var(--muted); }

  .folio {
    position: absolute;
    right: 83px;
    top: 524px;
    font-size: 13px;
    color: var(--ink);
  }
</style>
</head>
<body>
  <main class="spread">
    <section class="page page--dark">
      <blockquote class="quote">
        The connoisseur does not drink wine but tastes its secrets
        <cite class="attribution">—Tomas Verrand</cite>
      </blockquote>
      <p class="bio">Tomas Esteban Verrand i Moll, 1st Baron of Solbri and Vall d'Orena<br>(1911–1976) Catalan Printmaker and Stage Designer.</p>
    </section>
    <section class="page page--light">
      <blockquote class="quote">
        Wine is the divine juice of September
        <cite class="attribution">—Marchetti</cite>
      </blockquote>
      <p class="bio">Henri-Paul Daveline known by his “nom de plume” Marchetti.<br>(1702–1769). Savoyard Essayist, Diarist and Playwright.</p>
      <span class="folio">25</span>
    </section>
  </main>
</body>
</html>
```